Redesign of an existing homepage

This site needs a redesign
https://www.wanderhof-kelbach.de
This page with the accommodation options is important for the customer
https://www.wanderhof-kelbach.de/gastgeber/
Till now there is a new logo. See attachment. That's all I have.
It would make sense to use the colors of the logo in the redesign.
footer.jpg.
I would put this info into the footer. The graphic (Infomaterial) is not needed.
a new menu - links.jpg
This info can be put in a new menu. Therefore the right column is gone and there is more space for the design.
NEW:
Please keep in mind that the Icons are important and shall be displayed under every accommodation

```html
<!DOCTYPE html>
<html lang="en">
<head>
<meta charset="utf-8">
<title>Tourismusverband Kelbachtal – Holiday in the Rottal</title>
<link href="https://fonts.googleapis.com/css2?family=Poppins:ital,wght@0,300;0,400;0,500;0,600;0,700;1,700&display=swap" rel="stylesheet">
<style>
:root{
  --blue:#1568b2;
  --blue-dark:#0d5ea6;
  --sky:#2aa7df;
  --green:#86bc25;
  --text:#333;
  --white:#fff;
}
*{margin:0;padding:0;box-sizing:border-box}
html,body{width:1200px;height:5348px;overflow:hidden}
body{position:relative;font-family:'Poppins',sans-serif;color:var(--text);background:var(--white)}
.abs{position:absolute}
.topbar{left:0;top:0;width:1200px;height:40px;background:var(--blue)}
.topbar ul{list-style:none;display:flex;position:absolute;right:65px;top:11px;gap:0}
.topbar li{font-size:13px;color:#fff;margin-left:64px}
.mainnav{left:0;top:40px;width:1200px;height:56px;background:#fff;z-index:3}
.mainnav ul{list-style:none;display:flex;position:absolute;right:40px;top:22px}
.mainnav li{font-size:13px;color:#333;margin-left:44px;position:relative}
.mainnav li.active::after{content:"";position:absolute;left:0;right:0;bottom:-7px;height:2px;background:var(--green)}
.brand{left:50px;top:0;width:280px;height:190px;z-index:4;text-align:center}
.brand .mark{width:110px;height:110px;border-radius:50%;background:#fff;margin:8px auto 0;border:4px solid var(--sky)}
.brand .name{font-size:22px;font-weight:700;color:var(--blue);line-height:1.25;margin-top:10px}
.hero{left:0;top:96px;width:1200px;height:940px;background:linear-gradient(180deg,#c7dcef 0%,#8fb6d9 30%,#6c8e9f 50%,#40627a 75%,#2f4f6a 100%)}
.hero-title{left:0;width:1200px;top:688px;text-align:center;color:#fff;font-weight:700;font-size:62px;letter-spacing:-1px}
.hero-sub{left:0;width:1200px;top:778px;text-align:center;color:#fff;font-size:42px;font-weight:300}
.btn{display:flex;align-items:center;justify-content:center;border-radius:30px;color:#fff;font-weight:500}
.hero-btn{left:485px;top:858px;width:230px;height:56px;background:var(--sky);font-size:26px}
.hero-wave{left:0;top:900px;width:1200px;height:140px}
.photo{background:linear-gradient(160deg,#c9b08a,#7a5a3a)}
.circle{border-radius:50%}
.intro-photo{left:95px;top:1135px;width:450px;height:450px;background:linear-gradient(160deg,#f2e3cf 0%,#c8884b 55%,#5b3a22 100%)}
.intro h2{font-size:33px;font-weight:400;color:#222;line-height:1.15}
.intro{left:568px;top:1105px;width:565px}
.intro p{font-size:13px;line-height:1.85;margin-top:22px;color:#333}
.intro .claim{font-size:24px;font-weight:700;font-style:italic;color:var(--green);margin-top:20px}
.sec-title{font-size:46px;color:var(--blue);font-weight:400;line-height:1.2;letter-spacing:.5px}
.rule{width:76px;height:3px;background:var(--green);position:relative;margin-top:22px}
.rule::after{content:"";position:absolute;right:-4px;top:-4px;width:11px;height:11px;border-radius:50%;background:var(--green)}
.copy{font-size:13.5px;line-height:1.78;color:#333}
.btn-blue{background:var(--blue);font-size:20px;width:180px;height:50px}
.host{left:70px;top:1835px;width:490px}
.host .copy{margin-top:42px}
.host .btn{margin-top:40px}
.ring{overflow:visible}
.host-photo{left:660px;top:1816px;width:450px;height:450px;background:linear-gradient(180deg,#a8c4dc 0%,#c9b898 40%,#5f8c3c 70%,#4a7a2c 100%)}
.video{left:70px;top:2490px;width:1065px;height:506px;border-radius:28px;background:linear-gradient(180deg,#5f6b5a 0%,#8f8a70 40%,#c7b890 60%,#4e5a45 100%)}
.deco-disc{left:1065px;top:2428px;width:140px;height:140px;background:var(--blue)}
.play{left:558px;top:2688px;width:84px;height:84px;border:3px solid rgba(255,255,255,.8);background:rgba(255,255,255,.35)}
.video-title{left:70px;top:2835px;width:1000px;text-align:center;color:#fff;font-size:46px;font-weight:300;line-height:1.25}
.discover{left:62px;top:3205px;width:460px}
.discover .copy{margin-top:44px;font-size:13px}
.discover .copy p+p{margin-top:26px}
.discover .btn{margin-top:62px}
.tile{background:linear-gradient(160deg,#d8a25c,#8a4a22)}
.leisure-photo{left:118px;top:3983px;width:426px;height:426px;background:linear-gradient(180deg,#2f7fd0 0%,#7fb2e6 35%,#5b8f3e 55%,#1d4e9e 75%,#2a64b8 100%)}
.leisure{left:618px;top:4020px;width:520px}
.leisure .copy{margin-top:46px;font-size:13px}
.leisure .btn{margin-top:40px}
.contact-bg{left:0;top:4480px;width:1200px;height:580px}
.contact{left:72px;top:4640px;width:500px;color:#fff}
.contact h2{font-size:46px;font-weight:400;color:#fff}
.contact .bar{width:48px;height:2px;background:#fff;margin-top:18px}
.contact p{font-size:13px;margin-top:30px}
.field{position:absolute;background:#fff;font-size:12px;color:#555;padding:12px 20px}
.submit{left:70px;top:5010px;width:192px;height:54px;background:var(--green);font-size:18px}
.contact-photo{left:695px;top:4620px;width:418px;height:418px;background:linear-gradient(180deg,#6ea7d8 0%,#aac9e2 40%,#c9574a 70%,#3b3a35 100%);border:10px solid var(--green)}
.footer{left:0;top:5058px;width:1200px;height:254px;background:var(--blue-dark);color:#fff}
.footer h3{font-size:18px;font-weight:600;position:absolute}
.footer .line{position:absolute;height:1px;background:rgba(255,255,255,.35)}
.footer .txt{position:absolute;font-size:12.5px;line-height:1.75}
.ico{position:absolute;width:32px;height:32px;border-radius:50%;background:#fff}
.ico svg{position:absolute;left:8px;top:8px}
.legal{left:0;top:5312px;width:1200px;height:36px;background:var(--green);color:#fff;font-size:11.5px;text-align:center;line-height:36px}
</style>
</head>
<body>

<div class="abs topbar">
  <ul><li>Parish churches</li><li>Rottal-Inn</li><li>Thermal region</li><li>Hill Country Tourism Office</li></ul>
</div>
<nav class="abs mainnav">
  <ul><li class="active">Home</li><li>Host</li><li>Rottal</li><li>Leisure time</li><li>Excursion destinations</li><li>Art and Culture</li><li>Contact</li></ul>
</nav>
<div class="abs brand">
  <div class="mark"></div>
  <div class="name">TOURISMUSVERBAND KELBACHTAL</div>
</div>

<header>
  <div class="abs hero" role="img" aria-label="Photo: lake surrounded by reeds and forest, an angler sitting in a rowing boat"></div>
  <svg class="abs hero-wave" viewBox="0 0 1200 140" preserveAspectRatio="none">
    <path d="M0 60 C250 -10 500 150 800 120 C980 100 1100 60 1200 40 L1200 140 L0 140 Z" fill="#fff"/>
    <path d="M0 60 C250 -10 500 150 800 120 C980 100 1100 60 1200 40 L1200 70 C1100 90 980 125 800 135 C500 150 250 10 0 90 Z" fill="var(--blue)"/>
  </svg>
  <h1 class="abs hero-title">HOLIDAY IN THE ROTTAL</h1>
  <div class="abs hero-sub">The most beautiful spot in Bavaria</div>
  <div class="abs btn hero-btn">Contact Us</div>
</header>

<section>
  <div class="abs circle intro-photo" role="img" aria-label="Photo collage: twin church towers, horse sculpture and a lively town square"></div>
  <div class="abs intro">
    <h2>The Rottal-Inn holiday region is characterized by beautiful scenery and varied leisure activities.</h2>
    <p>Find peace and activity, culture and enjoyment… always combined with the warmth of your hosts and the positive attitude to life in this region. Here, you can forget everyday life and enjoy life consciously and at a slower pace.</p>
    <p>Explore the beautiful nature on a leisurely walk or bike ride through the rolling hills of the Rottal, past numerous sights.</p>
    <p>A wide variety of attractions for young and old, such as thermal baths, adventure pools, museums as well as numerous events and festivals guarantee eventful and unforgettable holidays.</p>
    <div class="claim">Discover the Rottal at its most beautiful!</div>
  </div>
</section>

<section>
  <div class="abs host">
    <h2 class="sec-title">HOST IN THE ROTTAL</h2>
    <div class="rule"></div>
    <p class="copy">Our holiday farm, in a quiet, idyllic location, offers many recreational opportunities, such as campfires, table tennis, barbecues, and cycling. Meadows and forests stretch right outside our front door. In the forest and by the stream, you can experience pure nature and recover from the stresses of everyday life. Our apartments are ideal for self-catering workmen. The covered patio invites you to spend relaxing hours in any weather. Other amenities: Bicycle rental | E-bike rental | Washing machine | Indian tent | Campfire with stick bread | XXL trampoline | Night hike | Baby equipment</p>
    <div class="btn btn-blue">View More</div>
  </div>
  <svg class="abs ring" style="left:635px;top:1792px" width="500" height="500" viewBox="0 0 500 500">
    <circle cx="250" cy="250" r="245" fill="none" stroke="var(--green)" stroke-width="2.5" stroke-dasharray="2 5"/>
    <path d="M85 70 A245 245 0 0 1 430 85 A245 245 0 0 1 430 415" fill="none" stroke="var(--blue)" stroke-width="2.5" stroke-dasharray="2 5"/>
    <circle cx="80" cy="68" r="7" fill="var(--green)"/>
    <circle cx="428" cy="418" r="7" fill="var(--blue)"/>
  </svg>
  <div class="abs circle host-photo" role="img" aria-label="Photo: farmhouse with balconies, children riding ponies on the lawn"></div>
</section>

<section>
  <div class="abs circle deco-disc"></div>
  <div class="abs video" role="img" aria-label="Video still: aerial view of two onion-domed church towers above the town"></div>
  <div class="abs circle play">
    <svg width="78" height="78" viewBox="0 0 78 78"><path d="M33 27 L51 39 L33 51 Z" fill="var(--blue)"/></svg>
  </div>
  <div class="abs video-title">Gästeverein<br>Kelbachtal</div>
</section>

<section>
  <div class="abs discover">
    <h2 class="sec-title">DISCOVER, EXPERIENCE AND ENJOY THE ROTTAL!</h2>
    <div class="rule"></div>
    <div class="copy">
      <p>The Rottal-Inn holiday region is characterized by beautiful scenery and varied leisure activities.</p>
      <p>Find peace and activity, culture and enjoyment… always combined with the warmth of your hosts and the positive attitude to life in this region. Here, you can forget everyday life and enjoy life consciously and at a slower pace.</p>
    </div>
    <div class="btn btn-blue">View More</div>
  </div>
  <div class="abs tile" style="left:557px;top:3325px;width:185px;height:190px;background:linear-gradient(160deg,#e0b070,#9a5a2a)" role="img" aria-label="Photo: hotel courtyard with arcades"></div>
  <div class="abs tile" style="left:557px;top:3525px;width:185px;height:190px;background:linear-gradient(160deg,#b6d29a,#c05050)" role="img" aria-label="Photo: beer garden with flowers"></div>
  <div class="abs tile" style="left:752px;top:3255px;width:185px;height:260px;background:linear-gradient(180deg,#6fa3dc,#d49a8a 60%,#6a6a6a)" role="img" aria-label="Photo: town hall with clock tower"></div>
  <div class="abs tile" style="left:752px;top:3525px;width:185px;height:265px;background:linear-gradient(180deg,#e08a3a,#b85a2a 60%,#3a3a50)" role="img" aria-label="Photo: colourful town houses with crowd"></div>
  <div class="abs tile" style="left:946px;top:3325px;width:185px;height:190px;background:linear-gradient(160deg,#e8c080,#9a6030)" role="img" aria-label="Photo: museum interior with wooden beams"></div>
  <div class="abs tile" style="left:946px;top:3525px;width:185px;height:190px;background:linear-gradient(180deg,#b8cbd6,#4aa8d0)" role="img" aria-label="Photo: indoor thermal pool"></div>
</section>

<section>
  <svg class="abs ring" style="left:96px;top:3960px" width="470" height="470" viewBox="0 0 470 470">
    <circle cx="235" cy="235" r="230" fill="none" stroke="var(--green)" stroke-width="2.5" stroke-dasharray="2 5"/>
    <path d="M75 70 A230 230 0 0 1 400 75 A230 230 0 0 1 400 395" fill="none" stroke="var(--blue)" stroke-width="2.5" stroke-dasharray="2 5"/>
    <circle cx="75" cy="70" r="7" fill="var(--green)"/>
    <circle cx="403" cy="397" r="7" fill="var(--blue)"/>
  </svg>
  <div class="abs circle leisure-photo" role="img" aria-label="Photo: outdoor swimming pool with lanes and trees"></div>
  <div class="abs leisure">
    <h2 class="sec-title">LEISURE IN THE ROTTAL</h2>
    <div class="rule"></div>
    <p class="copy">Leisure and relaxation for the whole family<br>Enjoy peace and relaxation in nature – combined with select activities. Get active with cycling, walking, and hiking, or simply unwind. Explore the region according to your needs!</p>
    <div class="btn btn-blue">View More</div>
  </div>
</section>

<section>
  <svg class="abs contact-bg" viewBox="0 0 1200 580" preserveAspectRatio="none">
    <path d="M0 40 C200 0 350 120 600 100 C850 80 1000 0 1200 20 L1200 580 L0 580 Z" fill="var(--sky)"/>
  </svg>
  <div class="abs contact">
    <h2>CONTACT US</h2>
    <div class="bar"></div>
    <p>Please fill out the form below and click submit to contact us. Thank you!</p>
  </div>
  <div class="field" style="left:72px;top:4800px;width:233px;height:40px">Your Name</div>
  <div class="field" style="left:325px;top:4800px;width:233px;height:40px">Phone Number</div>
  <div class="field" style="left:72px;top:4855px;width:486px;height:40px">Email Address</div>
  <div class="field" style="left:72px;top:4910px;width:486px;height:82px">Message</div>
  <div class="abs btn submit">Submit Now</div>
  <div class="abs circle contact-photo" role="img" aria-label="Photo: horse statue in front of a clock tower"></div>
</section>

<footer class="abs footer">
  <h3 style="left:76px;top:32px">CONTACT US</h3>
  <div class="line" style="left:76px;top:60px;width:585px"></div>
  <div class="ico" style="left:76px;top:88px"><svg width="16" height="16" viewBox="0 0 16 16"><path d="M8 1a5 5 0 0 0-5 5c0 4 5 9 5 9s5-5 5-9a5 5 0 0 0-5-5zm0 7a2 2 0 1 1 0-4 2 2 0 0 1 0 4z" fill="var(--blue)"/></svg></div>
  <div class="txt" style="left:115px;top:86px">Tourist Association of Kelbachtal<br>and Surrounding Areas<br>Mühlweg 12<br>84999 Kelbachtal</div>
  <div class="ico" style="left:428px;top:92px"><svg width="16" height="16" viewBox="0 0 16 16"><path d="M4 1l3 3-2 2c1 2 3 4 5 5l2-2 3 3-2 3C7 15 1 9 1 3z" fill="var(--blue)"/></svg></div>
  <div class="txt" style="left:472px;top:96px">Tel.: 08123 / 456 7890</div>
  <div class="ico" style="left:428px;top:132px"><svg width="16" height="16" viewBox="0 0 16 16"><rect x="2" y="6" width="12" height="7" fill="var(--blue)"/><rect x="4" y="2" width="8" height="4" fill="var(--blue)"/></svg></div>
  <div class="txt" style="left:472px;top:136px">Fax: 08123 / 456 7899</div>
  <div class="ico" style="left:428px;top:172px"><svg width="16" height="16" viewBox="0 0 16 16"><rect x="1" y="3" width="14" height="10" fill="var(--blue)"/><path d="M1 3l7 6 7-6" fill="none" stroke="#fff" stroke-width="1.2"/></svg></div>
  <div class="txt" style="left:472px;top:176px">info@kelbachtal-gaeste.de</div>
  <h3 style="left:825px;top:32px">OPENING HOURS:</h3>
  <div class="line" style="left:825px;top:60px;width:305px"></div>
  <div class="txt" style="left:825px;top:92px;line-height:2.55">Mon–Fri 9:00 – 17:00<br>May–October:<br>Sat 9:00–12:00</div>
</footer>
<div class="abs legal">Copyright © 2025 All Rights Reserved By Company name</div>

</body>
</html>
```